Business card design for a dynamic IT consulting company

We need a business card design for a young firm, specialized in the Telecommunications/Consulting industry. The name of the company is Quindor and Partners Business Consulting Ltd. (Short name: Quindor and Partnes)
Quindor = solve read reverse, so we aim to be uncomplicated and solution-oriented. The small pipe in our logo is also related to the word solve. So we need a new business card design, which is simple, eye catching and something non traditional (I would probably prefer a square shaped design rather than a rectangle, but open for suggestions). Attached our logo.

Target Market(s)

Usually our customers are Tier1 Telecoms providers (Q-Netra, Palorix, etc) and their executives.

Industry/Entity Type

Business

Contact Information for Business Card

Name: Bence Tolnavari
Email: b.tolnavari@quindor.hu
Web: www.quindor.hu
Mobile: +36 30 518 2769
Title: Managing Director

Optional:
Company name: Quindor and Partners Ltd.
Address: 1087 Budapest, Tolvenka str. 28/C, Hungary

Font styles to use
Other font styles liked:
• helveticaneue_medium, Prime Regular are used now.

Colors

Designer to choose colors to be used in the design.

Requirements
Must have
• I would like to have a 2 sided design.
Nice to have
• I thought if we make the logo a bit bigger (without the company name), that could go to the back with the company name below. I though, if the pipe in the logo is somehow touchable on the business card, would be nice and unique.

```html
<!DOCTYPE html>
<html lang="en">
<head>
<meta charset="utf-8">
<title>Quindor and Partners – Business Card</title>
<link href="https://fonts.googleapis.com/css2?family=Exo+2:wght@400&family=Work+Sans:wght@400;500&display=swap" rel="stylesheet">
<style>
  :root {
    --stage: #1b1b1c;
    --card-white: #ffffff;
    --brand-blue: #1a8fd3;
    --back-blue: #139bd9;
    --brand-magenta: #b5318f;
    --ink-grey: #555a60;
    --ink-dark: #3c4045;
  }
  * { margin: 0; padding: 0; box-sizing: border-box; }
  html, body {
    width: 1200px; height: 897px; overflow: hidden;
    background: var(--stage);
  }
  .canvas { position: relative; width: 1200px; height: 897px; }

  .card {
    position: absolute; left: 303px; width: 595px; height: 339px;
    border-radius: 19px; overflow: hidden;
  }
  .card--front { top: 92px; background: var(--card-white); }
  .card--back  { top: 469px; background: var(--back-blue); }

  .brand {
    position: absolute; display: flex; align-items: center;
    font-family: "Exo 2", sans-serif; font-weight: 400; white-space: nowrap;
  }
  .brand__square { display: block; }
  .card--front .brand { left: 38px; top: 38px; gap: 14px; font-size: 34px; color: var(--ink-grey); }
  .card--front .brand__square { width: 30px; height: 30px; background: var(--brand-magenta); }
  .card--back .brand { left: 54px; top: 138px; gap: 20px; font-size: 50px; color: #fff; }
  .card--back .brand__square { width: 48px; height: 48px; background: #fff; }

  .person { position: absolute; left: 42px; top: 184px; }
  .person__name {
    font-family: "Exo 2", sans-serif; font-size: 21px; color: var(--brand-blue);
    letter-spacing: 0.5px; line-height: 1;
  }
  .person__title {
    margin-top: 9px; font-family: "Work Sans", sans-serif; font-size: 14px; color: var(--ink-grey);
  }

  .contact {
    position: absolute; left: 351px; top: 168px;
    font-family: "Work Sans", sans-serif; font-size: 13.5px; color: var(--ink-dark);
  }
  .contact__list { list-style: none; }
  .contact__item { display: flex; align-items: center; gap: 10px; height: 19px; }
  .contact__icon { width: 12px; height: 12px; flex: none; }
  .contact__company {
    margin-top: 10px; font-family: "Exo 2", sans-serif; font-size: 15px; color: var(--brand-blue);
  }
  .contact__address { margin-top: 2px; line-height: 17px; }

  .front-band { position: absolute; left: 0; bottom: 0; width: 595px; height: 339px; }

  .back-web {
    position: absolute; left: 0; right: 0; top: 297px; text-align: center;
    font-family: "Work Sans", sans-serif; font-size: 15px; letter-spacing: 2.2px; color: #fff;
  }
</style>
</head>
<body>
<main class="canvas">

  <section class="card card--front" aria-label="Card front">
    <div class="brand">
      <span class="brand__square"></span>
      <span class="brand__name">Quindor &amp; Partners</span>
    </div>

    <div class="person">
      <p class="person__name">BENCE TOLNAVARI</p>
      <p class="person__title">Managing Director</p>
    </div>

    <div class="contact">
      <ul class="contact__list">
        <li class="contact__item">
          <svg class="contact__icon" viewBox="0 0 24 24" aria-hidden="true"><path fill="#1a8fd3" d="M6.6 10.8a15.1 15.1 0 0 0 6.6 6.6l2.2-2.2c.3-.3.7-.4 1-.2 1.1.4 2.3.6 3.6.6.6 0 1 .4 1 1V20c0 .6-.4 1-1 1A17 17 0 0 1 3 4c0-.6.4-1 1-1h3.5c.6 0 1 .4 1 1 0 1.3.2 2.5.6 3.6.1.3 0 .7-.2 1z"/></svg>
          <span>+36 30 518 2769</span>
        </li>
        <li class="contact__item">
          <svg class="contact__icon" viewBox="0 0 24 24" aria-hidden="true"><path fill="#1a8fd3" d="M2 5h20v14H2z"/><path fill="none" stroke="#fff" stroke-width="2" d="M3 6l9 7 9-7"/></svg>
          <span>b.tolnavari@quindor.hu</span>
        </li>
        <li class="contact__item">
          <svg class="contact__icon" viewBox="0 0 24 24" aria-hidden="true"><g fill="none" stroke="#1a8fd3" stroke-width="2"><circle cx="12" cy="12" r="10"/><ellipse cx="12" cy="12" rx="4.5" ry="10"/><path d="M2 12h20M4 7h16M4 17h16"/></g></svg>
          <span>www.quindor.hu</span>
        </li>
      </ul>
      <p class="contact__company">QUINDOR AND PARTNERS LTD.</p>
      <p class="contact__address">1087 Budapest, Tolvenka<br>str. 28/C, Hungary</p>
    </div>

    <svg class="front-band" viewBox="0 0 595 339" aria-hidden="true">
      <path fill="#b5318f" d="M0 330 H330 C360 330 368 314 400 314 H595 V339 H0 Z"/>
      <path fill="#1a8fd3" d="M0 321 H346 C340 323 336 326 330 326 H0 Z"/>
    </svg>
  </section>

  <section class="card card--back" aria-label="Card back">
    <div class="brand">
      <span class="brand__square"></span>
      <span class="brand__name">Quindor &amp; Partners</span>
    </div>
    <p class="back-web">www.quindor.hu</p>
  </section>

</main>
</body>
</html>
```